Velvet Pressings Techno Label Business Card

I'm looking for a very clean business card for my Velvet Pressings music label. The label focusses on techno music. The card should include:

• my name : Tomas Brandt as "Founder & CEO"
• email address: tomas@velvet-pressings.example
• web: www.velvet-pressings.example
• facebook logo + /velvetpress
• twitter logo + /velvetpress
• soundcloud logo + /velvetpressings

Feel free to include your ideas! I'm looking forward to discuss about it.

Tomas

Industry/Entity Type

Business

Contact Information for Business Card

I don't like glossy cards. Prefer matt.

Requirements
Nice to have
• Maybe on one side the complete logo, other side just the icon.
Should not have
• Flashy stuff. Must be clean and business like style.

```html
<!DOCTYPE html>
<html lang="en">
<head>
<meta charset="utf-8">
<title>Velvet Pressings – Business Card</title>
<link rel="stylesheet" href="https://fonts.googleapis.com/css2?family=Open+Sans:wght@400;600;700&display=swap">
<style>
  :root {
    --backdrop: #3a3330;
    --card: #0b0b0c;
    --accent: #f26a10;
    --muted: #8a8a8a;
    --contact: #b5b5b5;
  }
  * { margin: 0; padding: 0; box-sizing: border-box; }
  html, body { width: 1200px; height: 768px; overflow: hidden; }
  body {
    background: var(--backdrop);
    font-family: "Open Sans", Arial, sans-serif;
    position: relative;
  }
  .card {
    position: absolute;
    top: 234px;
    width: 500px;
    height: 300px;
    background: var(--card);
    border-radius: 3px;
    box-shadow: 0 10px 28px rgba(0,0,0,.45);
  }
  .card--front { left: 60px; }
  .card--back  { left: 640px; }

  /* Front: full wordmark */
  .wordmark {
    position: absolute;
    left: 0; right: 0; top: 50%;
    transform: translateY(-50%);
    display: flex;
    align-items: center;
    justify-content: center;
    gap: 16px;
  }
  .wordmark__dot {
    width: 34px; height: 34px;
    border-radius: 50%;
    background: var(--accent);
  }
  .wordmark__name {
    font-weight: 700;
    font-size: 36px;
    letter-spacing: -0.5px;
    color: var(--accent);
  }

  /* Back: icon + contact block */
  .brand-dot {
    position: absolute;
    left: 48px; top: 62px;
    width: 160px; height: 160px;
    border-radius: 50%;
    background: var(--accent);
  }
  .person {
    position: absolute;
    left: 258px; top: 78px;
  }
  .person__name {
    font-size: 19px;
    font-weight: 400;
    letter-spacing: 0.5px;
    color: var(--accent);
    line-height: 1.2;
  }
  .person__role {
    font-size: 11px;
    color: var(--muted);
    margin-top: 2px;
  }
  .contact-list {
    position: absolute;
    left: 246px; top: 160px;
    list-style: none;
  }
  .contact-list li {
    display: flex;
    align-items: center;
    gap: 9px;
    font-size: 13px;
    color: var(--contact);
    line-height: 22px;
  }
  .contact-icon {
    width: 12px; height: 12px;
    flex: none;
  }
  .contact-icon--social {
    background: var(--accent);
    border-radius: 2px;
  }
</style>
</head>
<body>

  <section class="card card--front" aria-label="Card front">
    <div class="wordmark">
      <span class="wordmark__dot" aria-hidden="true"></span>
      <span class="wordmark__name">Velvet Pressings</span>
    </div>
  </section>

  <section class="card card--back" aria-label="Card back">
    <span class="brand-dot" aria-hidden="true"></span>

    <div class="person">
      <p class="person__name">Tomas Brandt</p>
      <p class="person__role">Founder &amp; CEO</p>
    </div>

    <ul class="contact-list">
      <li>
        <svg class="contact-icon" viewBox="0 0 12 12" aria-hidden="true">
          <rect x="0.5" y="2" width="11" height="8" fill="var(--accent)"/>
          <path d="M0.5 2 L6 6.5 L11.5 2" fill="none" stroke="var(--card)" stroke-width="1"/>
        </svg>
        tomas@velvet-pressings.example
      </li>
      <li>
        <svg class="contact-icon" viewBox="0 0 12 12" aria-hidden="true">
          <circle cx="6" cy="6" r="5.5" fill="var(--accent)"/>
          <path d="M0.5 6 H11.5 M6 0.5 V11.5" stroke="var(--card)" stroke-width="0.9"/>
          <ellipse cx="6" cy="6" rx="2.4" ry="5.5" fill="none" stroke="var(--card)" stroke-width="0.9"/>
        </svg>
        www.velvet-pressings.example
      </li>
      <li><span class="contact-icon contact-icon--social" aria-hidden="true"></span>/velvetpress</li>
      <li><span class="contact-icon contact-icon--social" aria-hidden="true"></span>/velvetpress</li>
      <li><span class="contact-icon contact-icon--social" aria-hidden="true"></span>/velvetpressings</li>
    </ul>
  </section>

</body>
</html>
```